Business Card for Multi-Brand Sportswear Company

We are looking for a business card which represents our company and the multiple brands within it.

The company: Fen Athletics (LTD)
The brands: Fen, TavaPuni, ElmStretch, Grit and Rain

Employees using these cards would be representing Fen Athletics, rather than any of the individual brands. You will see a current design within the uploaded files, to give some inspiration. The actual text of the brands is not necessary, but the logos should be on there is some format.

Our creative minds on this are stretched, so we are looking for someone to make this their own, and show us what a good business card should look like.

We may like to get these printed with spot gloss, so keep that in mind with your designs.

www.fenathletics.co.uk

Industry/Entity Type

Business

Contact Information for Business Card

Leo Pemberton-Hale
Operations Manager
(+44) 1632 960 418
Leo@fenathletics.co.uk
www.fenathletics.co.uk

Font styles to use
Sans Serif
Other font styles liked:
• Eurostile

Colors
ffffff

Requirements
Nice to have
• Dark (black) background

```html
<!DOCTYPE html>
<html lang="en">
<head>
<meta charset="utf-8">
<title>Fen Athletics – Business Card</title>
<link href="https://fonts.googleapis.com/css2?family=Saira:wght@400;600&display=swap" rel="stylesheet">
<style>
  :root {
    --page-bg: #ebebeb;
    --card-dark: #262626;
    --card-mid: #333333;
    --accent-red: #e31b23;
    --text-white: #ffffff;
    --text-soft: #d8d8d8;
    --brand-grey: #9a9a9a;
  }
  * { box-sizing: border-box; margin: 0; padding: 0; }
  html, body {
    width: 1200px; height: 586px; overflow: hidden;
    background: var(--page-bg);
    font-family: "Saira", sans-serif;
    color: var(--text-white);
  }
  .card {
    position: absolute; top: 129px;
    width: 501px; height: 300px;
    overflow: hidden;
  }
  .card--front { left: 65px; }
  .card--back { left: 608px; }
  .card__texture {
    position: absolute; inset: 0;
    background: linear-gradient(135deg, var(--card-mid) 0%, var(--card-dark) 45%, var(--card-mid) 75%, var(--card-dark) 100%);
  }
  .tab {
    position: absolute; width: 15px; background: var(--accent-red);
  }
  .tab--left { left: 0; border-radius: 0 8px 8px 0; }
  .tab--right { right: 0; border-radius: 8px 0 0 8px; }
  .card--front .tab { top: 58px; height: 185px; }
  .card--back .tab { top: 50px; height: 200px; }

  .wordmark { position: absolute; display: flex; flex-direction: column; }
  .wordmark__line { display: flex; align-items: center; gap: 10px; }
  .wordmark__dot { background: var(--accent-red); display: block; }
  .wordmark__name { font-weight: 400; color: var(--text-white); line-height: 1; }
  .wordmark__tag { letter-spacing: 0.14em; font-weight: 400; color: var(--text-white); }

  .card--front .wordmark { left: 0; right: 0; top: 132px; align-items: center; }
  .card--front .wordmark__dot { width: 14px; height: 14px; }
  .card--front .wordmark__name { font-size: 40px; }
  .card--front .wordmark__tag { font-size: 12px; margin-top: 4px; margin-left: 130px; }

  .card--back .wordmark { right: 28px; top: 108px; align-items: flex-end; }
  .card--back .wordmark__dot { width: 10px; height: 10px; }
  .card--back .wordmark__name { font-size: 28px; }
  .card--back .wordmark__tag { font-size: 8px; margin-top: 2px; }

  .person { position: absolute; right: 32px; top: 22px; text-align: right; }
  .person__name { font-size: 18px; font-weight: 600; }
  .person__title { font-size: 12px; color: var(--text-soft); }

  .brands {
    position: absolute; right: 28px; top: 160px;
    display: flex; gap: 14px; list-style: none;
    font-size: 10px; color: var(--brand-grey);
  }

  .contact { position: absolute; left: 30px; top: 188px; list-style: none; }
  .contact__item { display: flex; align-items: center; gap: 8px; height: 24px; font-size: 11.5px; }
  .contact__icon { width: 14px; height: 12px; fill: var(--accent-red); }
  .address { position: absolute; left: 30px; top: 262px; font-size: 13px; font-weight: 600; }
</style>
</head>
<body>
  <section class="card card--front">
    <div class="card__texture" role="img" aria-label="Dark faceted polygon texture"></div>
    <span class="tab tab--left"></span>
    <span class="tab tab--right"></span>
    <div class="wordmark">
      <div class="wordmark__line">
        <span class="wordmark__dot"></span>
        <span class="wordmark__name">Fen Athletics</span>
      </div>
      <span class="wordmark__tag">PERFORMANCE WEAR</span>
    </div>
  </section>

  <section class="card card--back">
    <div class="card__texture" role="img" aria-label="Dark faceted polygon texture"></div>
    <span class="tab tab--left"></span>
    <span class="tab tab--right"></span>
    <div class="person">
      <p class="person__name">Ross Hartley</p>
      <p class="person__title">Managing Director</p>
    </div>
    <div class="wordmark">
      <div class="wordmark__line">
        <span class="wordmark__dot"></span>
        <span class="wordmark__name">Fen Athletics</span>
      </div>
      <span class="wordmark__tag">PERFORMANCE WEAR</span>
    </div>
    <ul class="brands">
      <li>ElmStretch</li>
      <li>Grit and Rain</li>
      <li>TavaPuni</li>
      <li>Fen</li>
    </ul>
    <ul class="contact">
      <li class="contact__item">
        <svg class="contact__icon" viewBox="0 0 14 12"><path d="M1 3c0-2 12-2 12 0v1h-3V3H4v1H1zM3 5h8l2 6H1z"/></svg>
        <span>+44 (0)1632 960418</span>
      </li>
      <li class="contact__item">
        <svg class="contact__icon" viewBox="0 0 14 12"><path d="M3 0h8v3H3zM0 4h14v5h-3V7H3v2H0zM4 8h6v4H4z"/></svg>
        <span>(555) 014-2276</span>
      </li>
      <li class="contact__item">
        <svg class="contact__icon" viewBox="0 0 14 12"><path d="M0 1h14v10H0zM1 2l6 5 6-5v1L7 8 1 3z" fill-rule="evenodd"/></svg>
        <span>ross@fenathletics.co.uk</span>
      </li>
    </ul>
    <p class="address">Kestrel Yard, Marlow Fen, FN4 2QT</p>
  </section>
</body>
</html>
```